Verdant Systems Business Card

want the back of card to be blue- with the logo in the center
front of card- info plus logo (info being mailing address, email address, and website address )
4 different names with titles to have on cards
1) Calvin Borsted - Owner
2) Naomi Trelvik- Customer Relationship Specialist
3) Felix Andrade- Vice President of Sales
4) Owen Markby- Chief Technology Officer

Target Market(s)

tech company in the government/probation office industry

Industry/Entity Type

Government Office

Contact Information for Business Card

1) Calvin Borsted - Owner

Colors
0355a3
ffffff

Requirements
Must have
• back side should be blue, with the logo placed in the center
• front side needs to include both the logo, as well as company info (info should include website address, email address, and mailing address)

```html
<!DOCTYPE html>
<html lang="en">
<head>
<meta charset="utf-8">
<title>Verdant Systems Business Card</title>
<link rel="stylesheet" href="https://fonts.googleapis.com/css2?family=Montserrat:wght@700&family=Fira+Sans:wght@400;500&display=swap">
<style>
  :root {
    --backdrop: #2a2a2c;
    --navy: #1c3566;
    --navy-deep: #16294f;
    --navy-light: #2a4a85;
    --paper: #ffffff;
    --grey-text: #7a7a7a;
    --grey-rule: #9a9a9a;
    --stripe: #a9abb0;
  }
  * { margin: 0; padding: 0; box-sizing: border-box; }
  html, body { width: 1200px; height: 900px; overflow: hidden; }
  body { background: var(--backdrop); position: relative; font-family: "Fira Sans", sans-serif; }

  .card { position: absolute; width: 700px; height: 400px; left: 250px; overflow: hidden; box-shadow: 0 12px 30px rgba(0,0,0,.45); }

  /* Back side */
  .card-back { top: 30px; background: var(--navy); }
  .back-field { position: absolute; inset: 0; background: linear-gradient(120deg, var(--navy-deep) 0%, var(--navy) 55%, var(--navy-light) 100%); }
  .back-brand { position: absolute; left: 0; right: 0; top: 50%; transform: translateY(-50%); display: flex; align-items: center; justify-content: center; gap: 14px; }
  .back-brand .brand-square { width: 22px; height: 22px; background: var(--paper); }
  .back-brand .brand-name { color: var(--paper); font-size: 30px; font-weight: 500; letter-spacing: 2px; text-transform: uppercase; }

  /* Front side */
  .card-front { top: 465px; background: var(--paper); }
  .person-name { position: absolute; left: 60px; top: 78px; font-family: "Montserrat", sans-serif; font-weight: 700; font-size: 27px; color: var(--navy); letter-spacing: .5px; text-transform: uppercase; }
  .person-title { position: absolute; left: 60px; top: 118px; font-size: 16px; color: var(--grey-text); }
  .brand-mark { position: absolute; right: 40px; top: 88px; display: flex; align-items: center; gap: 12px; }
  .brand-mark .brand-square { width: 20px; height: 20px; background: var(--navy); }
  .brand-mark .brand-name { font-size: 30px; font-weight: 500; color: var(--navy); letter-spacing: 1.5px; text-transform: uppercase; }
  .divider { position: absolute; left: 60px; right: 40px; top: 160px; height: 2px; background: var(--grey-rule); }
  .contact-list { position: absolute; left: 60px; top: 215px; list-style: none; }
  .contact-list li { display: flex; align-items: center; gap: 12px; font-size: 19px; color: var(--grey-text); line-height: 30px; }
  .contact-list svg { width: 16px; height: 16px; fill: var(--navy); }
  .address { position: absolute; right: 40px; top: 262px; text-align: right; font-size: 18px; line-height: 26px; color: var(--grey-text); }
  .footer-band { position: absolute; left: 0; bottom: 0; width: 700px; height: 90px; }
  .website { position: absolute; right: 40px; bottom: 14px; font-size: 19px; color: var(--paper); letter-spacing: 1px; }
</style>
</head>
<body>

<section class="card card-back" aria-label="Card back">
  <div class="back-field" role="img" aria-label="Repeating pattern of the company emblem on navy"></div>
  <div class="back-brand">
    <span class="brand-square"></span>
    <span class="brand-name">Verdant Systems</span>
  </div>
</section>

<section class="card card-front" aria-label="Card front">
  <h1 class="person-name">Calvin Borsted</h1>
  <p class="person-title">Owner</p>

  <div class="brand-mark">
    <span class="brand-square"></span>
    <span class="brand-name">Verdant Systems</span>
  </div>

  <div class="divider"></div>

  <ul class="contact-list">
    <li>
      <svg viewBox="0 0 16 16" aria-hidden="true"><path d="M3.6 1.2l2.2 2.6c.3.4.3.9 0 1.3L4.7 6.3c.9 2 2.5 3.7 4.6 4.8l1.2-1.1c.4-.3.9-.3 1.3 0l2.6 2.1c.4.3.4.9.1 1.3l-1.2 1.3c-.5.5-1.2.7-1.9.5C6.3 13.8 2.3 9.7.9 4.6.7 3.9.9 3.2 1.4 2.7L2.3 1.2c.4-.4 1-.4 1.3 0z"/></svg>
      <span>123-456-2100</span>
    </li>
    <li>
      <svg viewBox="0 0 16 16" aria-hidden="true"><path d="M0 3h16v1.2L8 9 0 4.2z"/><path d="M0 5.6l8 4.8 8-4.8V13H0z"/></svg>
      <span>youremail@mailbox.com</span>
    </li>
  </ul>

  <p class="address">Your address, city<br>state, ZIP 0000</p>

  <svg class="footer-band" viewBox="0 0 700 90" aria-hidden="true">
    <path d="M0 10 H270 L262 20 H0 Z" fill="var(--stripe)"/>
    <path d="M0 30 H282 Q292 12 312 12 H700 V90 H0 Z" fill="var(--navy)"/>
  </svg>
  <p class="website">www.yourwebsite.com</p>
</section>

</body>
</html>
```